Corporate Design - Immobilienverwaltungsgesellschaft
Zielgruppe
An- und Verkauf, Verwaltung und Vermietung von Immobilien
Zielgruppen: Immobilienspekulanten, Wohnungskäufer, Mieter, Vermieter
Aufgabenstellung
Wir suchen ein hochwertiges Design für eine in Gründung befindliche Gesellschaft mit beschränkter Haftung.
Diese wird aus 2 Gesellschaftern, Katrin und Torsten Fellmer bestehen.
Das Hauptziel der Gesellschaft wird der An- und Verkauf von Immobilien bis zu 1. Million Euro je Kaufobjekt sein
Mit dem Nachnamen der Gesellschafter kann auch gespielt werden, beispielsweise bei Abkürzungen. Die Bezeichnung F&F Verwaltungsgesellschaft mbH ist nicht zwingend, lediglich das Kürzel 'mbH' oder auch 'GmbH' ist aufgrund der Rechtsform der Gesellschaft zwingend aufzunehmen.
Diverse Designideen haben wir bereits vorliegen; hierauf kann aufgebaut werden, siehe Uploads
Unter anderem eine Anlehnung an die unter derselben Firmenadresse der Gesellschaft bestehende Rechtsanwaltskanzlei und deren Cooperate Design wäre eine Idee, jedoch keine zwingende Voraussetzung.

```html
<!DOCTYPE html>
<html lang="de">
<head>
<meta charset="utf-8">
<title>F&amp;F Verwaltungsgesellschaft mbH – Briefbogen</title>
<link rel="stylesheet" href="https://fonts.googleapis.com/css2?family=Source+Sans+3:wght@400;600&display=swap">
<style>
  :root {
    --brand-navy: #0b4a8a;
    --brand-blue: #0a84c0;
    --ink: #1d1d1b;
    --footer-dark: #3a3a3c;
    --paper: #fdfdfd;
    --fold-mark: #b5b5b5;
  }
  * { margin: 0; padding: 0; box-sizing: border-box; }
  html, body { width: 849px; height: 1200px; overflow: hidden; background: #fff; }
  body { font-family: "Source Sans 3", "Helvetica Neue", Arial, sans-serif; color: var(--ink); }

  .letterhead { position: relative; width: 849px; height: 1200px; background: var(--paper); overflow: hidden; }

  .brand-name {
    position: absolute; right: 41px; top: 72px;
    text-align: right; color: var(--brand-navy); font-weight: 600; line-height: 1;
  }
  .brand-name .brand-short { display: block; font-size: 34px; letter-spacing: 2px; }
  .brand-name .brand-full { display: block; font-size: 13.5px; letter-spacing: 1.2px; margin-top: 6px; text-transform: uppercase; }

  .sender-line {
    position: absolute; left: 101px; top: 184px;
    font-size: 9.2px; letter-spacing: -0.1px;
    padding-bottom: 1px; border-bottom: 1.3px solid var(--brand-blue);
  }

  .contact-column {
    position: absolute; left: 642px; top: 183px; height: 193px;
    border-left: 1.3px solid var(--brand-navy);
    padding-left: 15px; font-size: 11px; line-height: 15.7px;
  }
  .contact-column .label { margin-top: 1px; }
  .contact-column .manager { color: var(--brand-blue); font-weight: 600; }
  .contact-column .address { margin-top: 12px; }
  .contact-list { list-style: none; margin-top: 13px; }
  .contact-list li { display: flex; align-items: center; gap: 7px; }
  .contact-list svg { width: 11px; height: 11px; flex: none; }
  .contact-column .vat { margin-top: 12px; }

  .fold-mark { position: absolute; left: 0; height: 0; border-top: 0.8px solid var(--fold-mark); }
  .fold-top { top: 423px; width: 26px; }
  .fold-punch { top: 600px; width: 40px; }
  .fold-bottom { top: 848px; width: 26px; }

  .footer-waves { position: absolute; left: 0; top: 0; width: 849px; height: 1200px; }

  .bank-details {
    position: absolute; left: 84px; top: 1166px;
    color: #fff; font-size: 11px; letter-spacing: -0.1px;
  }
  .bank-details strong { font-weight: 600; }
  .bank-details .sep { color: var(--brand-blue); margin: 0 3px; }
</style>
</head>
<body>
<main class="letterhead">

  <div class="brand-name">
    <span class="brand-short">F&amp;F</span>
    <span class="brand-full">Verwaltungsgesellschaft mbH</span>
  </div>

  <p class="sender-line">F &amp; F Verwaltungsgesellschaft mbH • Lindenweg 12 • 66812 Talbrunn</p>

  <aside class="contact-column">
    <p class="label">Geschäftsführer:</p>
    <p class="manager">Katrin Fellmer</p>
    <p class="manager">Torsten Fellmer</p>
    <p class="address">Lindenweg 12<br>66812 Talbrunn</p>
    <ul class="contact-list">
      <li>
        <svg viewBox="0 0 12 12" aria-hidden="true"><path fill="#0a84c0" d="M2.3 1.2l1.8-.6 1.2 2.6-1.1.8c.5 1.3 1.4 2.3 2.6 2.9l.9-1 2.5 1.3-.6 1.8c-4 .3-7.7-3.7-7.3-7.8z"/></svg>
        06841 / 470 260
      </li>
      <li>
        <svg viewBox="0 0 12 12" aria-hidden="true" fill="none" stroke="#0a84c0" stroke-width="1"><rect x="3.5" y=".8" width="5" height="3"/><rect x="1" y="3.8" width="10" height="4.5" rx=".8"/><rect x="3.2" y="6.5" width="5.6" height="4.5"/><path d="M4.3 8.3h3.4M4.3 9.7h3.4"/></svg>
        06841 / 470 261
      </li>
      <li>
        <svg viewBox="0 0 12 12" aria-hidden="true"><rect x=".5" y="2.3" width="11" height="7.6" fill="#0a84c0"/><path d="M.8 2.6L6 6.6l5.2-4" fill="none" stroke="#fff" stroke-width=".9"/></svg>
        info@fundf-verwaltung.de
      </li>
      <li>
        <svg viewBox="0 0 12 12" aria-hidden="true" fill="none" stroke="#0a84c0" stroke-width=".9"><circle cx="6" cy="6" r="5"/><ellipse cx="6" cy="6" rx="2.2" ry="5"/><path d="M1 6h10M1.8 3.4h8.4M1.8 8.6h8.4"/></svg>
        www.fundf-verwaltung.de
      </li>
    </ul>
    <p class="vat">USt-IdNr. DE274019385</p>
  </aside>

  <span class="fold-mark fold-top"></span>
  <span class="fold-mark fold-punch"></span>
  <span class="fold-mark fold-bottom"></span>

  <svg class="footer-waves" viewBox="0 0 849 1200" aria-hidden="true">
    <path fill="var(--brand-blue)" d="M0 1026 C240 1122 540 1142 849 1124 L849 1131 C540 1152 240 1140 0 1061 Z"/>
    <path fill="var(--footer-dark)" d="M0 1069 C240 1148 540 1160 849 1147 L849 1200 L0 1200 Z"/>
  </svg>

  <p class="bank-details"><strong>Bankverbindung:</strong> Talbrunner Volksbank<span class="sep">•</span>BIC: TALBDE51XXX<span class="sep">•</span>IBAN: DE40 5907 1830 0462 1187 03</p>

</main>
</body>
</html>
```